Brightmoor Lift Inc Website Deisgn

We are a new small elevator contracting company.
We would like a full website designed similar to
http://pellingtonlifts.com or https://www.northvalelifting.ca/
In addition to contents found on the above webpages.. we would like a section for project gallery etc.... have fun with it ... make it professional

Target Market(s)

Elevator Consultants - Property managers - Condo Boards - Commercial office buildings

Coding

Number of Pages Required

5+ page

Requirements
Must have
• Navigation Bar.. Be view able via mobile ..Should be pictures of Tall Office buildings in background.. Toronto city skyline etc....

Have Fun!

```html
<!DOCTYPE html>
<html lang="en">
<head>
<meta charset="utf-8">
<title>Brightmoor Lift Inc</title>
<link href="https://fonts.googleapis.com/css2?family=Montserrat:wght@400;500;600;700&family=Arimo:wght@400;700&display=swap" rel="stylesheet">
<style>
:root{
  --blue:#1f7ae8;
  --blue-dark:#1462c7;
  --orange:#ff5a12;
  --ink:#111111;
  --text:#2d2d2d;
  --muted:#555555;
  --footer:#2b2321;
  --white:#ffffff;
}
*{margin:0;padding:0;box-sizing:border-box}
html,body{width:1200px;height:3859px;overflow:hidden;background:var(--white)}
body{position:relative;font-family:'Arimo',Arial,sans-serif;color:var(--text)}
.abs{position:absolute}
.heading{font-family:'Montserrat',Arial,sans-serif;font-weight:500;color:var(--ink);text-transform:uppercase}
.heading span{color:var(--blue)}
.btn{position:absolute;background:var(--orange);color:var(--white);font-family:'Arimo',Arial,sans-serif;text-transform:uppercase;display:flex;align-items:center;justify-content:center;border-radius:3px}

/* header */
.brand{left:113px;top:16px;display:flex;align-items:center;gap:12px;font-family:'Montserrat',Arial,sans-serif;font-weight:700;font-size:34px;color:var(--ink);letter-spacing:-.5px}
.brand-dot{width:44px;height:44px;border:4px solid var(--ink);border-radius:50%}
.top-contact{left:852px;font-size:17px;color:var(--ink);display:flex;align-items:center;gap:14px}
.top-contact.phone{top:11px;font-weight:700;font-size:19px}
.top-contact.mail{top:45px}
.nav{left:0;top:83px;width:1200px;height:57px;background:var(--blue)}
.nav a{position:absolute;top:19px;color:var(--white);font-size:15px;text-decoration:none;text-transform:uppercase}

/* hero */
.hero{left:0;top:140px;width:1200px;height:556px;background:linear-gradient(160deg,#5e5a58 0%,#9c7f68 30%,#6c6f74 55%,#3e444c 80%,#75797e 100%)}
.hero-title{left:0;top:305px;width:1200px;text-align:center;font-family:'Montserrat',Arial,sans-serif;font-weight:500;font-size:62px;color:var(--white)}
.hero-sub{left:180px;top:405px;width:840px;text-align:center;font-family:'Montserrat',Arial,sans-serif;font-size:20px;line-height:33px;color:var(--white)}
.dots{left:568px;top:649px;display:flex;gap:17px}
.dots i{width:11px;height:11px;border-radius:50%;background:var(--white)}

/* welcome */
.para{font-size:15px;line-height:32px;color:var(--text)}

/* expertise */
.expert-photo{left:0;top:1270px;width:532px;height:527px;background:linear-gradient(135deg,#d9d2c6,#bfb7aa 45%,#8f8a82 75%,#e7e2d9)}
.expert-panel{left:365px;top:1312px;width:835px;height:533px;background:linear-gradient(135deg,#1e78e6,#1561c6)}
.check{font-family:'Montserrat',Arial,sans-serif;font-size:16px;color:var(--white);display:flex;align-items:center;gap:10px}

/* services */
.card{top:2125px;width:315px;height:352px;border:1px solid #d6d6d6;box-shadow:0 1px 3px rgba(0,0,0,.15);text-align:center}
.card-photo{margin:1px 4px 0;height:213px;border:1px solid #6b9ad6}
.card h3{font-family:'Montserrat',Arial,sans-serif;font-weight:500;font-size:16px;color:var(--ink);margin-top:22px}
.card p{font-size:13.5px;line-height:26px;color:var(--muted);margin-top:8px;padding:0 20px}

/* cta */
.cta{left:0;top:2550px;width:1200px;height:210px;background:var(--blue)}

/* gallery */
.tile{position:absolute}

/* footer */
.footer{left:0;top:3470px;width:1200px;height:389px;background:var(--footer);color:var(--white)}
.foot-head{font-family:'Montserrat',Arial,sans-serif;font-weight:600;font-size:19px;color:var(--white);text-transform:uppercase}
.foot-text{font-size:14px;line-height:30px;color:var(--white)}
.social{width:38px;height:38px;border-radius:50%;background:var(--blue)}
.foot-icon{width:30px;height:30px;border:1px solid #9aa6b8;border-radius:50%;display:flex;align-items:center;justify-content:center}
</style>
</head>
<body>

<header>
  <div class="abs brand"><span class="brand-dot"></span>BRIGHTMOOR LIFT INC</div>
  <div class="abs top-contact phone">
    <svg width="18" height="18" viewBox="0 0 24 24"><path fill="#1f7ae8" d="M6.6 10.8a15 15 0 0 0 6.6 6.6l2.2-2.2c.3-.3.7-.4 1-.2 1.1.4 2.3.6 3.6.6.6 0 1 .4 1 1V20c0 .6-.4 1-1 1A17 17 0 0 1 3 4c0-.6.4-1 1-1h3.5c.6 0 1 .4 1 1 0 1.3.2 2.5.6 3.6.1.3 0 .7-.2 1z"/></svg>
    905 555 0142
  </div>
  <div class="abs top-contact mail">
    <svg width="18" height="14" viewBox="0 0 18 14"><rect width="18" height="14" rx="1" fill="#1f7ae8"/><path d="M1 1l8 7 8-7" stroke="#fff" stroke-width="1.5" fill="none"/></svg>
    info@brightmoorlift.ca
  </div>
  <nav class="abs nav">
    <a href="#" style="left:186px">Home</a>
    <a href="#" style="left:276px">About Us</a>
    <a href="#" style="left:400px">Our Services</a>
    <a href="#" style="left:559px">Employees</a>
    <a href="#" style="left:701px">FAQ</a>
    <a href="#" style="left:777px">Free Quote</a>
    <a href="#" style="left:920px">Contact Us</a>
  </nav>
</header>

<section>
  <div class="abs hero" role="img" aria-label="Looking up a tall glass elevator shaft in an office tower"></div>
  <h1 class="abs hero-title">Brightmoor Lift</h1>
  <p class="abs hero-sub">Lorem ipsum dolor sit amet, consectetur adipiscing elit, sed do eiusmod tempor incididunt ut labore et dolore magna .</p>
  <div class="btn" style="left:511px;top:500px;width:179px;height:50px;font-size:16px">Get Started</div>
  <div class="abs dots"><i></i><i></i><i></i></div>
</section>

<section>
  <h2 class="abs heading" style="left:116px;top:786px;font-size:31px">Welcome to <span>Brightmoor Lift</span></h2>
  <p class="abs para" style="left:113px;top:848px;width:548px;text-align:justify">Lorem ipsum dolor sit amet, consectetur adipiscing elit, sed do eiusmod tempor incididunt ut labore et dolore magna aliqua. Quis ipsum suspendisse ultrices and gravida. Risus commodo viverra maecenas accumsan lacus vel facilisis. Lorem ipsum dolor sit amet, consectetur adipiscing elit, sed do eiusmod tempor incidit labore et dolore magna aliqua. Quis ipsum suspendisse ultrices gravida. Risus commodo viverra maecenas accumsan lacus vel facilisis. sed do eiusmod tempor incididunt ut labore et dolore magna aliqua. Quis ipsum suspendisse udl gravida. Risus commodo viverra maecenas accumsan.</p>
  <div class="btn" style="left:113px;top:1128px;width:125px;height:42px;font-size:15px">Read More</div>
  <svg class="abs" style="left:700px;top:790px" width="420" height="445" viewBox="0 0 420 445">
    <defs>
      <linearGradient id="hexFill" x1="0" y1="0" x2="1" y2="1">
        <stop offset="0" stop-color="#3d5a80"/><stop offset=".5" stop-color="#a9b8c9"/><stop offset="1" stop-color="#2f4466"/>
      </linearGradient>
    </defs>
    <path d="M230 5 L405 110 Q418 118 418 133 L418 300 Q418 315 405 323 L250 418" fill="none" stroke="#1f7ae8" stroke-width="18"/>
    <path role="img" aria-label="Round glass panoramic elevator cabin" d="M205 18 Q212 14 219 18 L385 115 Q392 119 392 127 L392 318 Q392 326 385 330 L219 427 Q212 431 205 427 L15 318 Q8 314 8 306 L8 127 Q8 119 15 115 Z" fill="url(#hexFill)"/>
  </svg>
</section>

<section>
  <div class="abs expert-photo" role="img" aria-label="Glass home elevator beside a spiral staircase in a bright lobby"></div>
  <div class="abs expert-panel"></div>
  <h2 class="abs heading" style="left:575px;top:1392px;font-size:34px;line-height:52px;color:#fff">Expertise for innovative<br>custom solutions</h2>
  <p class="abs" style="left:577px;top:1513px;width:520px;font-size:14px;line-height:32px;color:#fff">Lorem ipsum dolor sit amet, consectetur adipiscing elit, sed do eiusmod tempor incididunt ut labore et dolore magna aliqua.</p>
  <div class="abs check" style="left:574px;top:1621px"><svg width="22" height="22" viewBox="0 0 22 22"><circle cx="11" cy="11" r="9.5" fill="none" stroke="#fff" stroke-width="1.6"/><path d="M6.5 11.5l3 3 6-6.5" fill="none" stroke="#fff" stroke-width="1.8"/></svg>Explosion-Proof Elevators</div>
  <div class="abs check" style="left:840px;top:1623px"><svg width="22" height="22" viewBox="0 0 22 22"><circle cx="11" cy="11" r="9.5" fill="none" stroke="#fff" stroke-width="1.6"/><path d="M6.5 11.5l3 3 6-6.5" fill="none" stroke="#fff" stroke-width="1.8"/></svg>Transit elevators</div>
  <div class="abs check" style="left:574px;top:1668px"><svg width="22" height="22" viewBox="0 0 22 22"><circle cx="11" cy="11" r="9.5" fill="none" stroke="#fff" stroke-width="1.6"/><path d="M6.5 11.5l3 3 6-6.5" fill="none" stroke="#fff" stroke-width="1.8"/></svg>Automobile elevators</div>
  <div class="abs check" style="left:840px;top:1668px"><svg width="22" height="22" viewBox="0 0 22 22"><circle cx="11" cy="11" r="9.5" fill="none" stroke="#fff" stroke-width="1.6"/><path d="M6.5 11.5l3 3 6-6.5" fill="none" stroke="#fff" stroke-width="1.8"/></svg>Inclined elevators</div>
  <div class="abs check" style="left:574px;top:1714px"><svg width="22" height="22" viewBox="0 0 22 22"><circle cx="11" cy="11" r="9.5" fill="none" stroke="#fff" stroke-width="1.6"/><path d="M6.5 11.5l3 3 6-6.5" fill="none" stroke="#fff" stroke-width="1.8"/></svg>Outdoor elevators</div>
  <div class="abs check" style="left:840px;top:1712px"><svg width="22" height="22" viewBox="0 0 22 22"><circle cx="11" cy="11" r="9.5" fill="none" stroke="#fff" stroke-width="1.6"/><path d="M6.5 11.5l3 3 6-6.5" fill="none" stroke="#fff" stroke-width="1.8"/></svg>Automobile parking machines</div>
</section>

<section>
  <h2 class="abs heading" style="left:0;top:1933px;width:1200px;text-align:center;font-size:38px">Our <span>Services</span></h2>
  <p class="abs" style="left:150px;top:2012px;width:900px;text-align:center;font-size:15px;line-height:32px">Lorem ipsum dolor sit amet, consectetur adipiscing elit, sed do eiusmod tempor incididunt ut labore et dolore magna aliqua. Quis ipsum suspendisse ultrices gravida. Risus commodo viverra maecenas accumsan lacus vel facilisis.</p>
  <div class="abs card" style="left:113px">
    <div class="card-photo" role="img" aria-label="Technician's toolbox at an open elevator door" style="background:linear-gradient(135deg,#3a2a1c,#8a6a3c 50%,#c9c4bb)"></div>
    <h3>Monthly Preventative Maintenance</h3>
    <p>Lorem ipsum dolor sit amet, consectetur adipiscing elit, sed do eiusmod</p>
  </div>
  <div class="abs card" style="left:455px">
    <div class="card-photo" role="img" aria-label="Modern glass elevator tower in an atrium" style="background:linear-gradient(135deg,#cfd6dc,#5d6670 50%,#e4e8ec)"></div>
    <h3>Modernization</h3>
    <p>Lorem ipsum dolor sit amet, consectetur adipiscing elit, sed do eiusmod</p>
  </div>
  <div class="abs card" style="left:797px">
    <div class="card-photo" role="img" aria-label="Elevator mechanic with a wrench at work" style="background:linear-gradient(135deg,#a7b4c2,#3f4f6a 55%,#d2a24a)"></div>
    <h3>Service &amp; Repair</h3>
    <p>Lorem ipsum dolor sit amet, consectetur adipiscing elit, sed do eiusmod</p>
  </div>
</section>

<section>
  <div class="abs cta"></div>
  <h2 class="abs heading" style="left:120px;top:2606px;font-size:28px;color:#fff">Are you ready for a better lift?</h2>
  <p class="abs" style="left:120px;top:2658px;width:700px;font-size:15px;line-height:32px;color:#fff">Lorem ipsum dolor sit amet, consectetur adipiscing elit, sed do eiusmod tempor incididunt ut labore et dolore magna aliqua. Quis ipsum suspendisse ultrices gravida.</p>
  <div class="btn" style="left:889px;top:2618px;width:188px;height:50px;font-size:17px;font-weight:700">Get Free Quote</div>
</section>

<section>
  <h2 class="abs heading" style="left:0;top:2844px;width:1200px;text-align:center;font-size:38px">Photo <span>Gallery</span></h2>
  <div class="tile" role="img" aria-label="Elevator shaft viewed from below with neon lights" style="left:113px;top:2943px;width:349px;height:429px;background:linear-gradient(180deg,#0f2a33,#3a6f80 45%,#b25a8c 60%,#10222a)"></div>
  <div class="tile" role="img" aria-label="Hand pressing an elevator call button panel" style="left:472px;top:2943px;width:312px;height:215px;background:linear-gradient(135deg,#c9cdd1,#6f7479 55%,#a7abb0)"></div>
  <div class="tile" role="img" aria-label="Closed steel elevator doors in a grey wall" style="left:795px;top:2943px;width:313px;height:215px;background:linear-gradient(135deg,#5d5a66,#8e8c95 50%,#4a4853)"></div>
  <div class="tile" role="img" aria-label="Round glass elevator cabins" style="left:472px;top:3165px;width:312px;height:207px;background:linear-gradient(135deg,#3d5a80,#b6c3d2 50%,#2f4466)"></div>
  <div class="tile" role="img" aria-label="Elevator machinery inside a shaft" style="left:795px;top:3165px;width:313px;height:207px;background:linear-gradient(135deg,#1c1a18,#6e5a40 50%,#2a2622)"></div>
</section>

<footer class="abs footer">
  <div class="abs" style="left:118px;top:62px;display:flex;align-items:center;gap:10px;font-family:'Montserrat',Arial,sans-serif;font-weight:700;font-size:20px;color:#fff"><span style="width:30px;height:30px;border:3px solid #fff;border-radius:50%"></span>BRIGHTMOOR LIFT INC</div>
  <p class="abs foot-text" style="left:117px;top:127px;width:300px">Lorem ipsum dolor sit amet, consectetur adipisc elit, sed do eiusmod tempor incidiut labore et dolore magna aliqua.</p>
  <div class="abs social" style="left:114px;top:236px"></div>
  <div class="abs social" style="left:162px;top:236px"></div>
  <div class="abs social" style="left:212px;top:236px"></div>

  <h3 class="abs foot-head" style="left:462px;top:62px">Conatcat Us</h3>
  <div class="abs foot-icon" style="left:462px;top:112px"><svg width="14" height="14" viewBox="0 0 24 24"><path fill="#1f7ae8" d="M6.6 10.8a15 15 0 0 0 6.6 6.6l2.2-2.2c.3-.3.7-.4 1-.2 1.1.4 2.3.6 3.6.6.6 0 1 .4 1 1V20c0 .6-.4 1-1 1A17 17 0 0 1 3 4c0-.6.4-1 1-1h3.5c.6 0 1 .4 1 1 0 1.3.2 2.5.6 3.6.1.3 0 .7-.2 1z"/></svg></div>
  <p class="abs foot-text" style="left:511px;top:112px;font-size:16px">(905) 555 0142</p>
  <div class="abs foot-icon" style="left:462px;top:162px"><svg width="12" height="15" viewBox="0 0 12 15"><path d="M6 0a6 6 0 0 1 6 6c0 4-6 9-6 9S0 10 0 6a6 6 0 0 1 6-6z" fill="#1f7ae8"/><circle cx="6" cy="6" r="2" fill="#2b2321"/></svg></div>
  <p class="abs foot-text" style="left:511px;top:162px;width:240px">48 Alder Grove Ave Westbury ON K0Z 1B2(Ashford)</p>
  <div class="abs foot-icon" style="left:462px;top:237px"><svg width="14" height="11" viewBox="0 0 18 14"><rect width="18" height="14" rx="1" fill="#1f7ae8"/><path d="M1 1l8 7 8-7" stroke="#2b2321" stroke-width="1.5" fill="none"/></svg></div>
  <p class="abs foot-text" style="left:511px;top:237px">dana.morrow@brightmoorlift.ca</p>

  <h3 class="abs foot-head" style="left:798px;top:62px">Subcribe&nbsp; Our Newsletter</h3>
  <p class="abs foot-text" style="left:800px;top:100px;font-size:13px">Lorem ipsum dolor sit amet, consectetur</p>
  <div class="abs" style="left:800px;top:150px;width:288px;height:48px;background:#fff;border-radius:2px">
    <span class="abs" style="left:22px;top:15px;font-size:14px;color:#888">Enter your Email</span>
    <div class="abs" style="left:231px;top:0;width:57px;height:48px;background:var(--blue);display:flex;align-items:center;justify-content:center;border-radius:0 2px 2px 0">
      <svg width="20" height="20" viewBox="0 0 20 20"><path d="M1 9L19 1 12 19 9 11z" fill="#fff"/></svg>
    </div>
  </div>

  <div class="abs" style="left:113px;top:353px;width:245px;height:1px;background:#777"></div>
  <p class="abs" style="left:0;top:344px;width:1200px;text-align:center;font-size:13px;color:#fff">Copyrights © 2020 Copyrights Company Name | All Rights Reserved</p>
  <div class="abs" style="left:842px;top:353px;width:245px;height:1px;background:#777"></div>
</footer>

</body>
</html>
```